TuneRoost - Music Industry App needs a top quality wordpress homepage

We need a modern responsive wordpress homepage built. Our website will only feature one page with the goal to get people to sign up to our app. A word document has been uploaded outlining the page content/sections.

Once the homepage is finalised, I will also need 2 landing pages built as part of this competition. It will be very similar to the homepage with the same layout etc but just feature different images and content. The homepage is for anyone (artists and venues) to find out about us but the landing pages will be artist or venue specific.

The completed work must be delivered as an exportable file into wordpress and be designed properly so no more work is needed to begin utilising as the actual website. The images used must be setup correctly for speed and quality also.

Target Market(s)

Venues and Artists.

Coding

Coded - Design and coding required

Requirements
Must have
• UPDATE: High Res Logo files attached
• Must be a modern looking website and be responsive. Must look good across all devices from desktop, to mobile and tablet. Needs to be very high quality.
• Please see the attached logo - I am waiting for the final high quality version and will reupload when complete but this will be enough to get you started for now. The website must have a dark base colour and have red/white elements to match the logo. The red colour used MUST match the red colour used in the logo.
• Please have a go at creating it how you think is best and provide feedback from there. I am leaving it very open to the designers so I can get the best website possible and lots of different ideas etc.

```html
<!DOCTYPE html>
<html lang="en">
<head>
<meta charset="utf-8">
<title>TuneRoost – Live music booking</title>
<link href="https://fonts.googleapis.com/css2?family=IBM+Plex+Sans:wght@400;500;600;700&family=Roboto:wght@700;900&display=swap" rel="stylesheet">
<style>
:root{
  --red:#e10b17;
  --black:#000;
  --ink:#1c1c1c;
  --text:#333;
  --muted:#9a9a9a;
  --paper:#fff;
  --mist:#f4f1f1;
  --line:#d8d8d8;
}
*{box-sizing:border-box;margin:0;padding:0}
html,body{width:1200px;height:4435px;overflow:hidden}
body{font-family:"IBM Plex Sans",Arial,sans-serif;color:var(--text);background:var(--paper);position:relative}
.section{position:absolute;left:0;width:1200px}
.abs{position:absolute}
.center{text-align:center}

/* header */
.site-header{top:0;height:169px;background:var(--black)}
.brand{position:absolute;display:flex;align-items:center;gap:10px;font-weight:600;color:var(--red)}
.brand .dot{width:34px;height:34px;border-radius:50%;background:var(--red)}
.site-header .brand{left:131px;top:56px;font-size:40px}
.search{left:611px;top:36px;width:276px;height:45px;background:#2b2b2b;color:#bbb;font-size:12px;padding:15px 22px}
.search svg{position:absolute;right:20px;top:15px}
.signup{left:907px;top:36px;width:162px;height:45px;background:var(--red);color:#fff;font-weight:700;font-size:13px;line-height:45px;text-align:center}
.nav{left:613px;top:118px;font-size:13px;color:#fff}
.nav a{color:#fff;text-decoration:none;position:absolute;white-space:nowrap}
.nav a.active{color:var(--red)}
.nav a.active::after{content:"";position:absolute;left:0;right:0;top:24px;height:2px;background:var(--red)}

/* hero */
.hero{top:169px;height:575px;background:radial-gradient(ellipse at 30% 20%,#4d4f9a 0%,#27244a 35%,#120d14 70%,#090707 100%)}
.hero-panel{left:284px;top:38px;width:625px;height:137px;background:rgba(0,0,0,.72);color:#fff;text-align:center}
.hero-panel h1{font-family:Roboto,sans-serif;font-weight:900;font-size:38px;margin-top:28px;letter-spacing:.5px}
.hero-panel p{font-size:18px;margin-top:8px}
.hero-form{left:284px;top:177px;width:625px;height:52px;background:#fff}
.field{position:absolute;display:flex;align-items:center;gap:10px;font-size:13px;color:#444}
.hero-form .field{left:22px;top:18px}
.hero-form .btn{position:absolute;left:383px;top:3px;width:239px;height:46px;background:var(--red);color:#fff;font-weight:700;font-size:18px;text-align:center;line-height:46px}
.dots{left:545px;top:516px;display:flex;gap:14px;align-items:center}
.dots span{width:9px;height:9px;border-radius:50%;background:#fff}
.dots span.on{width:15px;height:15px;border:3px solid var(--red);background:#fff}

/* section emblem */
.emblem{display:flex;align-items:center;justify-content:center}
.emblem .o-dot{width:40px;height:40px;border-radius:50%;background:var(--red)}
.section-title{font-size:33px;color:var(--ink);font-weight:400}

/* how */
.how{top:744px;height:775px;background:var(--paper)}
.step{position:absolute;width:180px;text-align:center;font-size:13px;line-height:17px;color:#333}
.step .num{display:block;font-size:27px;color:#aaa;margin-top:14px;font-weight:300}
.step-icon{position:absolute;width:110px;height:110px;border-radius:50%;background:var(--red);display:flex;align-items:center;justify-content:center}
.step-icon .inner{width:88px;height:88px;border-radius:50%;background:#111;display:flex;align-items:center;justify-content:center}
.hub{left:477px;top:179px;width:248px;height:248px;border-radius:50%;background:#0b0b0b;border:20px solid var(--red)}

/* why */
.why{top:1519px;height:507px;background:var(--mist)}
.feature{position:absolute;width:220px;text-align:center}
.feature .pic{width:104px;height:104px;border-radius:50%;margin:0 auto;background:#e6e3e3}
.feature .bar{width:26px;height:2px;background:var(--red);margin:24px auto 18px}
.feature h3{font-size:18px;font-weight:600;color:#111}
.feature p{font-size:14px;line-height:21px;margin-top:14px;color:#333}

/* audiences */
.audience{top:2026px;height:760px;background:var(--paper)}
.aud-col{position:absolute;top:0;width:430px}
.aud-col .emblem{justify-content:flex-start;position:absolute;top:62px;left:38px}
.aud-col h2{position:absolute;top:98px;font-size:34px;font-weight:400;color:#111}
.ticks{position:absolute;top:175px;list-style:none;width:380px}
.ticks li{position:relative;padding-left:30px;font-size:15px;line-height:21px;color:#222;margin-bottom:21px}
.ticks li svg{position:absolute;left:0;top:4px}
.aud-note{position:absolute;font-size:15px;line-height:21px;color:#222;width:430px}
.reg{position:absolute;top:622px;width:406px;height:57px;border:2px solid #ddd;background:#fff}
.reg .field{left:20px;top:18px}
.reg .btn{position:absolute;right:3px;top:4px;width:115px;height:45px;background:var(--red);color:#fff;font-weight:700;font-size:19px;text-align:center;line-height:45px}
.divider{left:591px;top:74px;width:5px;height:586px;background:#eee;border-left:1px solid #ddd}

/* about */
.about{top:2786px;height:523px;background:var(--mist)}
.about-photo{left:0;top:0;width:623px;height:523px;background:radial-gradient(ellipse at 70% 55%,#c33a5b 0%,#6a1c3d 40%,#2a0d1e 75%,#160711 100%)}
.about h2{left:683px;top:118px;font-size:34px;font-weight:400;color:#111}
.about p{left:683px;top:193px;width:386px;font-size:16px;line-height:23.2px;color:#333}
.about .btn{left:685px;top:413px;width:138px;height:40px;background:var(--red);color:#fff;font-weight:700;font-size:17px;text-align:center;line-height:40px}

/* contact */
.contact{top:3309px;height:775px;background:#f7f6f6}
.map{left:0;top:191px;width:622px;height:537px;background:linear-gradient(135deg,#e9e9e9,#dcdcdc 45%,#e6ebe3 100%)}
.contact-card{left:622px;top:255px;width:445px;height:404px;background:#fff;box-shadow:0 2px 14px rgba(0,0,0,.06)}
.c-item{position:absolute;left:63px;display:flex;gap:22px}
.c-icon{width:62px;height:62px;border-radius:50%;background:var(--red);display:flex;align-items:center;justify-content:center;flex:none}
.c-item h4{font-size:16px;font-weight:700;color:#222;margin-top:4px}
.c-item p{font-size:17px;line-height:23px;color:#333;margin-top:3px}

/* footer */
.site-footer{top:4084px;height:351px;background:var(--black);color:#fff}
.site-footer .brand{left:145px;top:123px;font-size:48px}
.site-footer .brand .dot{width:40px;height:40px}
.f-col{position:absolute;top:58px;font-size:11px;line-height:17px}
.f-col h5{font-size:11px;font-weight:700;letter-spacing:.5px;margin-bottom:19px}
.f-row{display:flex;align-items:flex-start;gap:14px;margin-bottom:16px}
.soc{display:flex;align-items:center;gap:14px;margin-bottom:13px}
.soc span.c{width:26px;height:26px;border-radius:50%;background:#1c4f9c}
.f-line{left:460px;top:263px;width:585px;height:1px;background:#333}
.copy{left:0;width:1200px;top:298px;text-align:center;font-size:10px;color:#ddd}
</style>
</head>
<body>

<header class="section site-header">
  <div class="brand"><span class="dot"></span>TuneRoost</div>
  <div class="abs search">SEARCH
    <svg width="12" height="12" viewBox="0 0 12 12"><circle cx="5" cy="5" r="3.6" fill="none" stroke="#ddd" stroke-width="1.6"/><path d="M7.6 7.6 11 11" stroke="#ddd" stroke-width="1.6"/></svg>
  </div>
  <div class="abs signup">SIGNUP FOR FREE</div>
  <nav class="abs nav">
    <a class="active" style="left:0">HOME</a>
    <a style="left:70px">ABOUT US</a>
    <a style="left:176px">MUSIC</a>
    <a style="left:262px">ARTISTS</a>
    <a style="left:361px">CONTACT US</a>
  </nav>
</header>

<section class="section hero" role="img" aria-label="Crowd with raised hands at a live concert under blue and purple stage lights">
  <div class="abs hero-panel">
    <h1>ZIPRIDE FOR LIVE MUSIC</h1>
    <p>TuneRoost connects venues with artists to make booking gigs simple</p>
  </div>
  <div class="abs hero-form">
    <div class="field"><svg width="16" height="12" viewBox="0 0 16 12"><rect x=".6" y=".6" width="14.8" height="10.8" fill="none" stroke="#555" stroke-width="1.2"/><path d="M.6.6 8 7l7.4-6.4" fill="none" stroke="#555" stroke-width="1.2"/></svg>E mail id</div>
    <div class="btn">Sign up now for FREE</div>
  </div>
  <div class="abs dots"><span></span><span></span><span class="on"></span><span></span><span></span></div>
</section>

<section class="section how">
  <svg class="abs" style="left:0;top:0" width="1200" height="775" aria-hidden="true">
    <polygon points="0,582 275,775 0,775" fill="#f4f1f1"/>
    <polygon points="1200,582 921,775 1200,775" fill="#f4f1f1"/>
    <g fill="none" stroke="#999" stroke-width="1.2" stroke-dasharray="2 3">
      <path d="M377 279 C410 300 390 390 470 386"/>
      <path d="M830 279 C795 300 815 390 732 386"/>
      <path d="M601 427 V515"/>
      <path d="M455 441 C470 420 500 420 520 427"/>
      <path d="M755 441 C740 420 705 420 685 427"/>
    </g>
  </svg>
  <div class="abs hub"></div>
  <div class="abs emblem" style="left:0;width:1200px;top:35px"><span class="o-dot"></span></div>
  <h2 class="abs section-title center" style="left:0;width:1200px;top:90px">How TuneRoost Works</h2>

  <div class="step-icon" style="left:267px;top:222px"><div class="inner"><svg width="42" height="36" viewBox="0 0 42 36"><rect x="2" y="5" width="38" height="29" rx="2" fill="#fff"/><rect x="15" y="0" width="12" height="8" fill="#fff" stroke="#111" stroke-width="2"/><circle cx="13" cy="17" r="4" fill="#111"/><path d="M6 29q7-9 14 0z" fill="#111"/><path d="M24 15h11M24 21h11M24 27h8" stroke="#111" stroke-width="2.4"/></svg></div></div>
  <div class="step" style="left:232px;top:350px">Artists and venues<br>sign up for free and<br>create a profile<span class="num">01</span></div>

  <div class="step-icon" style="left:365px;top:432px"><div class="inner"><svg width="36" height="44" viewBox="0 0 36 44"><circle cx="18" cy="16" r="14" fill="none" stroke="#fff" stroke-width="4"/><circle cx="18" cy="13" r="4.5" fill="#fff"/><path d="M10 23q8-8 16 0" fill="#fff"/><path d="M18 30v13" stroke="#fff" stroke-width="4"/></svg></div></div>
  <div class="step" style="left:330px;top:555px">Venues search for<br>an artist for their<br>upcoming gigs<span class="num">02</span></div>

  <div class="step-icon" style="left:546px;top:516px"><div class="inner"><svg width="40" height="40" viewBox="0 0 40 40"><rect x="3" y="7" width="28" height="28" rx="3" fill="none" stroke="#fff" stroke-width="3.5"/><path d="M15 26l2-7 16-16 5 5-16 16z" fill="#fff"/></svg></div></div>
  <div class="step" style="left:511px;top:642px">Venues request a quote<br>and communicate with<br>the artist direct<span class="num">03</span></div>

  <div class="step-icon" style="left:734px;top:432px"><div class="inner"><svg width="44" height="38" viewBox="0 0 44 38"><path d="M4 10h30l6 6v18H4z" fill="#fff"/><path d="M2 4l26 0 4 6H6z" fill="#fff"/><rect x="22" y="20" width="14" height="8" rx="2" fill="#111"/><circle cx="26" cy="24" r="1.6" fill="#fff"/></svg></div></div>
  <div class="step" style="left:699px;top:555px">The gig is booked in once<br>payment is provided<br>by the venue.<span class="num">04</span></div>

  <div class="step-icon" style="left:830px;top:222px"><div class="inner"><svg width="46" height="38" viewBox="0 0 46 38"><rect x="2" y="2" width="32" height="26" rx="2" fill="#fff"/><path d="M7 9h22M7 15h22M7 21h14" stroke="#111" stroke-width="2.4"/><circle cx="34" cy="27" r="10" fill="#fff" stroke="#111" stroke-width="2"/><path d="M29 27l4 4 6-7" fill="none" stroke="#111" stroke-width="2.4"/></svg></div></div>
  <div class="step" style="left:795px;top:342px">Upon completion the<br>money is paid to the<br>artist within 48 hours<br>or less.<span class="num">05</span></div>
</section>

<section class="section why">
  <div class="abs emblem" style="left:0;width:1200px;top:52px"><span class="o-dot"></span></div>
  <h2 class="abs section-title center" style="left:0;width:1200px;top:110px">Why TuneRoost?</h2>
  <div class="feature" style="left:103px;top:202px"><div class="pic" role="img" aria-label="Illustration of a booking screen"></div><div class="bar"></div><h3>Simple</h3><p>TuneRoost makes gig<br>booking easy for both the<br>venue and artist.</p></div>
  <div class="feature" style="left:357px;top:202px"><div class="pic" role="img" aria-label="Illustration of a handshake"></div><div class="bar"></div><h3>Connect</h3><p>Join the TuneRoost community<br>which is full of amazing<br>artists and venues.</p></div>
  <div class="feature" style="left:618px;top:202px"><div class="pic" role="img" aria-label="Illustration of a protective shield"></div><div class="bar"></div><h3>Protection</h3><p>Everyone is protected<br>with our complimentary<br>dispute resolutions.</p></div>
  <div class="feature" style="left:868px;top:202px"><div class="pic" role="img" aria-label="Illustration of a hand holding a coin"></div><div class="bar"></div><h3>Price</h3><p>Get the best rate possible<br>with TuneRoost only receiving<br>5% of the artists fee.</p></div>
</section>

<section class="section audience">
  <div class="abs divider"></div>

  <div class="aud-col" style="left:129px">
    <div class="emblem"><span class="o-dot" style="width:34px;height:34px"></span></div>
    <h2>Venues</h2>
    <ul class="ticks">
      <li><svg width="13" height="11"><path d="M1 6l4 4 7-9" fill="none" stroke="#e10b17" stroke-width="2.6"/></svg>TuneRoost is a 100% FREE service for all venues - you pay us nothing!</li>
      <li><svg width="13" height="11"><path d="M1 6l4 4 7-9" fill="none" stroke="#e10b17" stroke-width="2.6"/></svg>Get instant access to hundreds of artists around your local community</li>
      <li><svg width="13" height="11"><path d="M1 6l4 4 7-9" fill="none" stroke="#e10b17" stroke-width="2.6"/></svg>All genres to suit any venue from a pub to a wedding or even a nightclub</li>
      <li><svg width="13" height="11"><path d="M1 6l4 4 7-9" fill="none" stroke="#e10b17" stroke-width="2.6"/></svg>Simple booking process with a money back guarantee</li>
      <li><svg width="13" height="11"><path d="M1 6l4 4 7-9" fill="none" stroke="#e10b17" stroke-width="2.6"/></svg>Communicate directly with the artist and negotiate the price</li>
    </ul>
    <p class="aud-note" style="top:512px">TuneRoost is not yet ready to host gigs as we’re currently working on building our artists. We are launching for venues in Q4 2019. Pre-register now to keep informed and be one of the first people to use our platform.</p>
    <div class="reg" style="left:0">
      <div class="field"><svg width="16" height="12" viewBox="0 0 16 12"><rect x=".6" y=".6" width="14.8" height="10.8" fill="none" stroke="#555" stroke-width="1.2"/><path d="M.6.6 8 7l7.4-6.4" fill="none" stroke="#555" stroke-width="1.2"/></svg>E mail id</div>
      <div class="btn">Register</div>
    </div>
  </div>

  <div class="aud-col" style="left:670px">
    <div class="emblem"><span class="o-dot" style="width:34px;height:34px"></span></div>
    <h2>Artists</h2>
    <ul class="ticks">
      <li><svg width="13" height="11"><path d="M1 6l4 4 7-9" fill="none" stroke="#e10b17" stroke-width="2.6"/></svg>Sign up to TuneRoost for FREE and get yourself in front of venues</li>
      <li><svg width="13" height="11"><path d="M1 6l4 4 7-9" fill="none" stroke="#e10b17" stroke-width="2.6"/></svg>Only pay us if you get a gig - we only get 5% of the fee you charge the venue</li>
      <li><svg width="13" height="11"><path d="M1 6l4 4 7-9" fill="none" stroke="#e10b17" stroke-width="2.6"/></svg>All genres and artists welcome - as long as you’re experienced and professional</li>
      <li><svg width="13" height="11"><path d="M1 6l4 4 7-9" fill="none" stroke="#e10b17" stroke-width="2.6"/></svg>Get paid within 48 hours or less after the gig guaranteed!</li>
      <li><svg width="13" height="11"><path d="M1 6l4 4 7-9" fill="none" stroke="#e10b17" stroke-width="2.6"/></svg>Negotiate your price and don’t pay huge agent fees to ensure you earn top dollar</li>
    </ul>
    <p class="aud-note" style="top:578px">Sign up and create your TuneRoost profile now</p>
    <div class="reg" style="left:0">
      <div class="field"><svg width="16" height="12" viewBox="0 0 16 12"><rect x=".6" y=".6" width="14.8" height="10.8" fill="none" stroke="#555" stroke-width="1.2"/><path d="M.6.6 8 7l7.4-6.4" fill="none" stroke="#555" stroke-width="1.2"/></svg>E mail id</div>
      <div class="btn">Register</div>
    </div>
  </div>
</section>

<section class="section about">
  <div class="abs about-photo" role="img" aria-label="Close-up of a guitarist playing on stage under warm pink lights"></div>
  <div class="abs emblem" style="left:735px;top:70px"><span class="o-dot"></span></div>
  <h2 class="abs">About TuneRoost</h2>
  <p class="abs">Lorem ipsum dolor sit amet, consectetur adipiscing elit, sed do eiusmod tempor incididunt ut labore et dolore magna aliqua. Ut enim ad minim veniam, quis nostrud exercitation ullamco laboris nisi ut aliquip ex ea commodo consequat. Duis aute irure dolor in reprehenderit in voluptate velit esse cillum dolore eu fugiat nulla pariatur. Excepteur sint occaecat cupidatat non proident.</p>
  <div class="abs btn">Read More</div>
</section>

<section class="section contact">
  <div class="abs emblem" style="left:0;width:1200px;top:53px"><span class="o-dot"></span></div>
  <h2 class="abs section-title center" style="left:0;width:1200px;top:109px">Contact us</h2>
  <div class="abs map" role="img" aria-label="Street map of the surrounding area"></div>
  <div class="abs contact-card">
    <div class="c-item" style="top:58px">
      <div class="c-icon"><svg width="20" height="26" viewBox="0 0 20 26"><path d="M10 1a9 9 0 0 0-9 9c0 7 9 15 9 15s9-8 9-15a9 9 0 0 0-9-9z" fill="#fff"/><circle cx="10" cy="10" r="3.4" fill="#e10b17"/></svg></div>
      <div><h4>Address</h4><p>48 Larkspur Lane<br>Millbrook, OR 97011</p></div>
    </div>
    <div class="c-item" style="top:167px">
      <div class="c-icon"><svg width="24" height="24" viewBox="0 0 24 24"><path d="M5 2l4 1 2 5-3 2a13 13 0 0 0 6 6l2-3 5 2 1 4c-1 2-3 3-5 3C10 22 2 14 2 7c0-2 1-4 3-5z" fill="#fff"/></svg></div>
      <div><h4>Call Us</h4><p>555.010.2040</p></div>
    </div>
    <div class="c-item" style="top:267px">
      <div class="c-icon"><svg width="24" height="18" viewBox="0 0 24 18"><rect x="1" y="1" width="22" height="16" rx="1.5" fill="#fff"/><path d="M1 2l11 8 11-8" fill="none" stroke="#e10b17" stroke-width="1.8"/></svg></div>
      <div><h4>E mail Us</h4><p>info@tuneroost.com</p></div>
    </div>
  </div>
</section>

<footer class="section site-footer">
  <div class="brand"><span class="dot"></span>TuneRoost</div>
  <div class="f-col" style="left:460px">
    <h5>CONTACT US</h5>
    <div class="f-row"><svg width="9" height="12" viewBox="0 0 9 12"><path d="M4.5 0A4.5 4.5 0 0 0 0 4.5C0 8 4.5 12 4.5 12S9 8 9 4.5A4.5 4.5 0 0 0 4.5 0z" fill="#fff"/></svg><span>310 Harbor Row<br>Fairview, CA 90210</span></div>
    <div class="f-row"><svg width="10" height="10" viewBox="0 0 24 24"><path d="M5 2l4 1 2 5-3 2a13 13 0 0 0 6 6l2-3 5 2 1 4c-1 2-3 3-5 3C10 22 2 14 2 7c0-2 1-4 3-5z" fill="#fff"/></svg><span>555.010.2040</span></div>
    <div class="f-row"><svg width="11" height="9" viewBox="0 0 24 18"><rect x="1" y="1" width="22" height="16" fill="#fff"/><path d="M1 2l11 8 11-8" fill="none" stroke="#000" stroke-width="2"/></svg><span>hello@tuneroost.com</span></div>
  </div>
  <div class="f-col" style="left:739px">
    <h5>MENU</h5>
    <div>HOME<br>PRODUCT<br>SOLUTIONS<br>PLANS<br>CONTACT US</div>
  </div>
  <div class="f-col" style="left:952px">
    <h5>CONNECT WITH US</h5>
    <div class="soc"><span class="c"></span>Friendbook</div>
    <div class="soc"><span class="c" style="background:#1d8fd6"></span>Chirper</div>
    <div class="soc"><span class="c" style="background:#0e4a86"></span>WorkLink</div>
  </div>
  <div class="abs f-line"></div>
  <div class="abs copy">Copyright © 2019 All Rights Reserved</div>
</footer>

</body>
</html>
```